Business card design for Virtual Assistance company

I need a business card designed for my virtual assistance company. We are a small company who services primarily C-level executive clients. The card needs to be double sided with the following contact information on the back:
Melissa Thornbury
Owner/CEO
info@rkpadvisory.net
www.rkpadvisory.net
555.302.9817

The front side should just have the company name incorporated: "RKP Advisory" and "virtual assistance"

The card should be simplistic, but eye catching and should speak to high level executives. Our primary focus areas consist of executive assistance and government contracting.

Target Market(s)

CEOs and executives

Contact Information for Business Card

see project description. phone, email, website.

Colors

Designer to choose only greyscale colors for use in the design.

```html
<!DOCTYPE html>
<html lang="en">
<head>
<meta charset="utf-8">
<title>RKP Advisory – Business Card</title>
<link href="https://fonts.googleapis.com/css2?family=Libre+Baskerville:wght@400;700&family=Montserrat:wght@400;500&display=swap" rel="stylesheet">
<style>
  :root {
    --stage: #8a8a8a;
    --stage-dark: #5c5c5c;
    --ink: #111111;
    --paper: #ffffff;
    --paper-shade: #ececec;
    --rule: #333333;
    --muted: #222222;
  }
  * { margin: 0; padding: 0; box-sizing: border-box; }
  html, body { width: 1200px; height: 900px; overflow: hidden; }
  body {
    background: radial-gradient(ellipse at 50% 35%, var(--stage) 0%, var(--stage-dark) 100%);
    position: relative;
    font-family: "Montserrat", sans-serif;
  }
  .card {
    position: absolute;
    left: 320px;
    width: 560px;
    height: 320px;
    overflow: hidden;
    box-shadow: 0 10px 30px rgba(0,0,0,0.35);
  }
  .card--front { top: 100px; background: var(--ink); }
  .card--back  { top: 480px; background: linear-gradient(180deg, var(--paper) 0%, var(--paper-shade) 100%); }

  .front__pattern {
    position: absolute; inset: 0;
    background: linear-gradient(110deg, #2a2a2a 0%, #111 45%, #050505 100%);
  }
  .front__name {
    position: absolute; right: 70px; top: 120px;
    font-family: "Libre Baskerville", serif;
    font-size: 30px; color: var(--paper); font-weight: 400;
  }

  .back__swoosh { position: absolute; inset: 0; }
  .back__brand {
    position: absolute; left: 60px; top: 125px; width: 210px; text-align: right;
  }
  .brand__name {
    font-family: "Libre Baskerville", serif;
    font-size: 27px; color: var(--ink); font-weight: 400; white-space: nowrap;
  }
  .brand__tagline {
    font-family: "Libre Baskerville", serif;
    font-size: 11px; letter-spacing: 1.5px; color: var(--muted); margin-top: 6px;
  }
  .back__divider {
    position: absolute; left: 290px; top: 58px; width: 1px; height: 150px; background: var(--rule);
  }
  .back__contact { position: absolute; left: 308px; top: 54px; }
  .contact__name {
    font-family: "Libre Baskerville", serif; font-weight: 700; font-size: 19px; color: var(--ink);
  }
  .contact__title { font-size: 12px; color: var(--muted); margin: 4px 0 12px 22px; }
  .contact__list { list-style: none; }
  .contact__item {
    display: flex; align-items: center; gap: 8px;
    font-size: 13px; color: var(--muted); margin-bottom: 6px;
  }
  .contact__icon { width: 12px; height: 12px; flex: none; }
</style>
</head>
<body>

<section class="card card--front" aria-label="Card front">
  <div class="front__pattern" role="img" aria-label="Tonal black repeating company-name pattern"></div>
  <div class="front__name">RKP Advisory</div>
</section>

<section class="card card--back" aria-label="Card back">
  <svg class="back__swoosh" viewBox="0 0 560 320" preserveAspectRatio="none" aria-hidden="true">
    <path d="M0 240 C 160 300, 400 280, 560 200 L560 320 L0 320 Z" fill="#111"/>
    <path d="M60 262 C 250 262, 420 240, 510 172 C 420 250, 240 272, 60 262 Z" fill="#111"/>
  </svg>

  <div class="back__brand">
    <div class="brand__name">RKP Advisory</div>
    <div class="brand__tagline">VIRTUAL ASSISTANCE</div>
  </div>

  <div class="back__divider"></div>

  <div class="back__contact">
    <div class="contact__name">Melissa Thornbury</div>
    <div class="contact__title">Owner/CEO</div>
    <ul class="contact__list">
      <li class="contact__item">
        <svg class="contact__icon" viewBox="0 0 12 12"><path d="M2.5 1 L4.5 1 L5.2 3.6 L4 4.6 C4.7 6 6 7.3 7.4 8 L8.4 6.8 L11 7.5 L11 9.5 C11 10.3 10.3 11 9.5 11 C5 11 1 7 1 2.5 C1 1.7 1.7 1 2.5 1 Z" fill="#111"/></svg>
        555.302.9817
      </li>
      <li class="contact__item">
        <svg class="contact__icon" viewBox="0 0 12 12"><rect x="0.5" y="2" width="11" height="8" fill="#111"/><path d="M0.5 2 L6 6.5 L11.5 2" stroke="#fff" stroke-width="1" fill="none"/></svg>
        info@rkpadvisory.net
      </li>
      <li class="contact__item">
        <svg class="contact__icon" viewBox="0 0 12 12"><circle cx="6" cy="6" r="5.5" fill="#111"/><path d="M0.5 6 H11.5 M6 0.5 C3.5 3 3.5 9 6 11.5 M6 0.5 C8.5 3 8.5 9 6 11.5" stroke="#fff" stroke-width="0.7" fill="none"/></svg>
        www.rkpadvisory.net
      </li>
    </ul>
  </div>
</section>

</body>
</html>
```